Tallowood building company Business card design

I need a business card design for my company. I have a logo but dont have business cards with our logo..

www.tallowoodbuildingco.com.au

The logo is on the website

I need the same details as this design I have attached. we have changed the logo and colours. just like the website

Building

```html
<!DOCTYPE html>
<html lang="en">
<head>
<meta charset="utf-8">
<title>Tallowood Building – Business Card</title>
<link rel="stylesheet" href="https://fonts.googleapis.com/css2?family=EB+Garamond:wght@400;500&family=Encode+Sans+Condensed:wght@600&family=Signika:wght@400;600&display=swap">
<style>
  :root {
    --brand-blue: #1f7fc0;
    --band-grey: #b9bbbe;
    --ink: #2b2b2b;
    --muted: #7a7a7a;
    --rule: #9cc6e4;
    --card: #ffffff;
    --backdrop: #e9eaec;
  }
  * { margin: 0; padding: 0; box-sizing: border-box; }
  html, body { width: 1200px; height: 799px; overflow: hidden; }
  body {
    background: var(--backdrop);
    font-family: "Signika", Arial, sans-serif;
    position: relative;
  }
  .card {
    position: absolute;
    left: 120px; top: 120px;
    width: 960px; height: 560px;
    background: var(--card);
    box-shadow: 0 8px 24px rgba(0,0,0,.12);
    overflow: hidden;
  }
  .card-bands { position: absolute; inset: 0; }

  .brand-mark {
    position: absolute; left: 96px; top: 48px;
    width: 96px; height: 96px;
    background: var(--brand-blue);
  }
  .brand-name {
    position: absolute; left: 56px; top: 178px;
    font-family: "EB Garamond", Georgia, serif;
    font-weight: 500;
    color: var(--brand-blue);
    text-transform: uppercase;
    line-height: 1;
  }
  .brand-name .name-main { display: block; font-size: 56px; letter-spacing: 1px; }
  .brand-name .name-sub { display: block; font-size: 56px; letter-spacing: 1px; margin-top: 2px; }

  .tagline {
    position: absolute; left: 300px; top: 52px;
    font-family: "EB Garamond", Georgia, serif;
    font-size: 40px; line-height: 1.05;
    color: var(--ink);
    white-space: nowrap;
  }
  .tagline .accent { color: var(--brand-blue); }
  .tagline .line-two { display: block; padding-left: 150px; }

  .rule { position: absolute; height: 1px; background: var(--rule); }
  .rule-top { top: 328px; left: 40px; right: 110px; }
  .rule-bottom { top: 414px; left: 520px; right: 110px; }

  .contact-person {
    position: absolute; right: 110px; top: 338px; text-align: right;
  }
  .person-name {
    font-family: "Encode Sans Condensed", "Arial Narrow", sans-serif;
    font-weight: 600; font-size: 36px; line-height: 1.1; color: var(--brand-blue);
  }
  .person-role { font-size: 17px; line-height: 1.2; color: var(--muted); }

  .contact-details { position: absolute; left: 44px; top: 0; font-size: 21px; color: var(--ink); }
  .contact-details .label { color: var(--brand-blue); font-weight: 600; }
  .detail-phone { position: absolute; left: 0; top: 362px; white-space: nowrap; }
  .detail-mobile { position: absolute; left: 150px; top: 424px; white-space: nowrap; }
  .detail-web { position: absolute; left: 150px; top: 458px; white-space: nowrap; }
</style>
</head>
<body>
  <article class="card">
    <svg class="card-bands" width="960" height="560" viewBox="0 0 960 560" aria-hidden="true">
      <rect x="0" y="0" width="960" height="30" fill="var(--brand-blue)"/>
      <polygon points="230,30 960,30 960,176 280,176" fill="var(--band-grey)"/>
      <line x1="280" y1="178" x2="960" y2="178" stroke="var(--brand-blue)" stroke-width="2"/>
      <rect x="0" y="540" width="960" height="20" fill="var(--band-grey)"/>
    </svg>

    <div class="brand-mark"></div>
    <div class="brand-name">
      <span class="name-main">Tallowood</span>
      <span class="name-sub">Building</span>
    </div>

    <p class="tagline">
      <span class="accent">We build</span> unique
      <span class="line-two">&amp; beautiful <span class="accent">homes</span></span>
    </p>

    <div class="rule rule-top"></div>

    <div class="contact-person">
      <div class="person-name">Marek Dalton</div>
      <div class="person-role">Director</div>
    </div>

    <div class="rule rule-bottom"></div>

    <div class="contact-details">
      <div class="detail-phone"><span class="label">p:</span> 08 9417 2368</div>
      <div class="detail-mobile"><span class="label">m:</span> 0412 558 190 &nbsp;<span class="label">e:</span> info@tallowoodbuildingco.com.au</div>
      <div class="detail-web"><span class="label">www.</span>tallowoodbuildingco.com.au</div>
    </div>
  </article>
</body>
</html>
```